Update informational website

I need a new modern site design for my website.

Here is the site: http://q.zq/kpTr

Here is a theme I liked: http://q.zq/kpTm

I am looking for something with clean lines and an exciting designs and graphics, please use images from brindlecove.com and track the images used so I can buy them if I like the design.

I just need the homepage and one interior page designed.

Colors
Bright Green #6ed30d
Dark Text #222
Lighter Text #444

Number of Pages Required

2 page

Font styles to use
Sans Serif

Requirements
Must have
• Clean, good spacing, responsive design, high resolution design

```html
<!DOCTYPE html>
<html lang="en">
<head>
<meta charset="utf-8">
<title>Window Film Services – Saguaro Window Tint</title>
<link rel="stylesheet" href="https://fonts.googleapis.com/css2?family=Roboto:wght@400;500;700&family=Open+Sans:wght@400;600;700&display=swap">
<style>
:root{
  --green:#6ed30d;
  --green-dark:#57b000;
  --text-dark:#222;
  --text-light:#444;
  --white:#fff;
  --footer-bg:#151515;
  --footer-bottom:#0d0d0d;
  --line:#cfcfcf;
}
*{box-sizing:border-box;margin:0;padding:0}
html,body{width:1200px;height:2946px;overflow:hidden}
body{position:relative;background:var(--white);font-family:"Open Sans",Arial,sans-serif;color:var(--text-light)}
.abs{position:absolute}

/* hero */
.hero{left:0;top:0;width:1200px;height:470px;overflow:hidden}
.hero-photo{position:absolute;inset:0;background:linear-gradient(180deg,#3b3a36 0%,#5c5a52 35%,#2c2b28 75%,#1c1c1a 100%)}
.hero-shade{position:absolute;inset:0;background:radial-gradient(ellipse at 55% 45%,rgba(220,220,215,.35) 0%,rgba(0,0,0,0) 45%)}
.hero-curve{position:absolute;left:0;top:380px;width:1200px;height:90px}
.brand{left:100px;top:26px;display:flex;align-items:center;gap:12px}
.brand-dot{width:34px;height:34px;border-radius:50%;background:var(--green)}
.brand-name{font-family:"Roboto",Arial,sans-serif;font-weight:700;font-size:30px;color:var(--green);line-height:1}
.topbar{left:520px;top:30px;display:flex;gap:28px;font-family:"Roboto",Arial,sans-serif;font-size:12.5px;color:var(--white);align-items:center;white-space:nowrap}
.topbar span{display:flex;align-items:center;gap:9px}
.social{left:1000px;top:32px;display:flex;gap:12px}
.social i{display:block;width:12px;height:12px;border-radius:50%;background:var(--white)}
.nav{left:460px;top:80px;display:flex;gap:30px;font-family:"Roboto",Arial,sans-serif;font-weight:500;font-size:16px;color:var(--white)}
.nav .active{color:var(--green)}
.hero-title{left:0;top:258px;width:1200px;text-align:center;font-family:"Roboto",Arial,sans-serif;font-weight:500;font-size:30px;color:var(--white)}

/* intro */
.section-title{left:0;top:536px;width:1200px;text-align:center;font-family:"Roboto",Arial,sans-serif;font-weight:400;font-size:33px;color:var(--text-dark);letter-spacing:.3px}
.intro{left:140px;top:590px;width:920px;text-align:center;font-size:12.5px;line-height:23px;color:var(--text-light)}

/* service cards */
.card{width:456px}
.card-photo{width:456px;height:226px}
.card-icon{position:absolute;left:0;top:176px;width:102px;height:102px;border-radius:50%;background:var(--green);border:5px solid var(--white);display:flex;align-items:center;justify-content:center}
.card-title{position:absolute;left:0;top:296px;font-family:"Roboto",Arial,sans-serif;font-weight:400;font-size:25px;color:var(--text-dark)}
.card-sub{position:absolute;left:0;top:330px;font-family:"Roboto",Arial,sans-serif;font-weight:500;font-size:15px;color:var(--text-dark)}
.card-body{position:absolute;left:0;top:362px;width:456px;font-size:11.3px;line-height:20px;color:var(--text-light)}
.card-body p{margin-bottom:12px}

.photo-auto{background:linear-gradient(135deg,#6e8795 0%,#b9c8cf 45%,#2e7a86 100%)}
.photo-commercial{background:linear-gradient(160deg,#d9ecf8 0%,#4f8fc8 40%,#0f3f7a 100%)}
.photo-wraps{background:linear-gradient(135deg,#e8e8e6 0%,#8a9190 45%,#2e3333 100%)}
.photo-bra{background:linear-gradient(135deg,#1e3550 0%,#3d6688 45%,#0f1c2a 100%)}

/* map */
.map{left:0;top:2048px;width:1200px;height:480px;background:linear-gradient(180deg,#e6e3dc 0%,#dcdcd6 50%,#e3e1da 100%)}

/* footer */
.footer{left:0;top:2510px;width:1200px;height:338px;background:linear-gradient(180deg,#1f1f1f 0%,var(--footer-bg) 100%)}
.footer-edge{left:0;top:2500px;width:1200px;height:40px}
.foot-head{font-family:"Roboto",Arial,sans-serif;font-weight:500;font-size:18px;color:var(--white)}
.foot-links{list-style:none;font-size:12.5px;color:var(--white);line-height:26px}
.foot-links li{display:flex;align-items:center;gap:10px}
.foot-links li::before{content:"";width:5px;height:5px;border-top:1.5px solid var(--white);border-right:1.5px solid var(--white);transform:rotate(45deg)}
.contact-line{display:flex;gap:14px;font-size:12.5px;color:var(--white);line-height:20px}
.quote-text{font-size:12px;line-height:20px;color:var(--white)}
.field{border:1px solid #9a9a9a;height:44px;font-size:12px;color:var(--white);padding:14px 14px}
.signup{background:var(--green);height:44px;color:var(--white);font-family:"Roboto",Arial,sans-serif;font-weight:500;font-size:13px;display:flex;align-items:center;justify-content:center}
.bottom-bar{left:0;top:2848px;width:1200px;height:98px;background:var(--footer-bottom);border-top:1px solid #2a2a2a}
.copyright{left:100px;top:2888px;font-size:12px;color:var(--white)}
.foot-brand{left:528px;top:2880px;display:flex;align-items:center;gap:10px}
.foot-brand .brand-dot{width:24px;height:24px}
.foot-brand .brand-name{font-size:21px}
.foot-social{left:994px;top:2880px;display:flex;gap:8px}
.foot-social i{display:block;width:22px;height:22px;border-radius:50%;border:1px solid var(--white)}
</style>
</head>
<body>

<header class="hero abs">
  <div class="hero-photo" role="img" aria-label="White sedan driving along an autumn road at speed"></div>
  <div class="hero-shade"></div>
  <svg class="hero-curve" viewBox="0 0 1200 90" preserveAspectRatio="none">
    <path d="M0 14 Q600 120 1200 0 L1200 90 L0 90 Z" fill="var(--white)"/>
    <path d="M0 14 Q600 120 1200 0" fill="none" stroke="var(--green)" stroke-width="6"/>
  </svg>
</header>

<div class="brand abs"><span class="brand-dot"></span><span class="brand-name">Saguaro Window Tint</span></div>

<div class="topbar abs">
  <span><svg width="13" height="13" viewBox="0 0 24 24"><path d="M6.6 10.8a15 15 0 006.6 6.6l2.2-2.2c.3-.3.7-.4 1-.2 1.1.4 2.3.6 3.6.6.6 0 1 .4 1 1V20c0 .6-.4 1-1 1C10.6 21 3 13.4 3 4c0-.6.4-1 1-1h3.5c.6 0 1 .4 1 1 0 1.3.2 2.5.6 3.6.1.3 0 .7-.2 1z" fill="#fff"/></svg>GIVE US A CALL 480.555.0147</span>
  <span><svg width="14" height="11" viewBox="0 0 14 11"><rect x=".75" y=".75" width="12.5" height="9.5" fill="none" stroke="#fff" stroke-width="1.5"/><path d="M1 1l6 5 6-5" fill="none" stroke="#fff" stroke-width="1.5"/></svg>info@saguarotint.example</span>
</div>
<div class="social abs"><i></i><i></i><i></i><i></i><i></i></div>

<nav class="nav abs">
  <span>HOME</span><span class="active">WINDOW FILM SERVICES</span><span>ABOUT US</span><span>FILM</span><span>GALLERY</span><span>CONTACT US</span>
</nav>

<h1 class="hero-title abs">WINDOW FILM SERVICES</h1>

<h2 class="section-title abs">WINDOW FILM AT SAGUARO WINDOW TINT</h2>
<p class="intro abs">Saguaro Tinting is not just another tint shop. We specialize in one thing and one thing only: Window Tinting. We offer Residential, Commercial and Automotive tinting services. Our philosophy is simple; do things right the first time! After 18 years we have learned that there is no such thing as a small job. Whether you need your personal car tinted, your new home protected or a complete face lift on your 10 story building, we believe that quality installation</p>

<!-- Automotive film -->
<article class="card abs" style="left:100px;top:727px">
  <div class="card-photo photo-auto" role="img" aria-label="Installer in gloves applying film to a car window"></div>
  <div class="card-icon"><svg width="48" height="40" viewBox="0 0 48 40"><path d="M4 36V18L18 4h26v32z M8 18h34V8H20z" fill="none" stroke="#fff" stroke-width="3" stroke-linejoin="round"/><path d="M30 24h8" stroke="#fff" stroke-width="3"/></svg></div>
  <h3 class="card-title">Automotive Film</h3>
  <p class="card-sub">Heat, infrared, and UV protection</p>
  <div class="card-body">
    <p>Saguaro Tint owner Dale Moreno and his staff of professional installers work with two of the world's finest window film manufacturers, Norvane and Solacrest, whose superior products significantly reduce heat and UV rays while retaining color stability over long periods of solar exposure.</p>
    <p>The Norvane Crystalline Automotive Window Film is a multilayer film combining more than 200 layers thinner than a sticky note. While allowing 90% of light into your vehicle, these films reject up to 97% of heat-producing infrared light and block as much as 60% of the heat entering through your windows.</p>
    <p>The Norvane Color Stable film incorporates nano-carbon polyester, significantly reducing heat and blocking 99% of UV rays up to SPF1000 to protect both</p>
  </div>
</article>

<!-- Commercial & residential -->
<article class="card abs" style="left:644px;top:727px">
  <div class="card-photo photo-commercial" role="img" aria-label="Glass office tower facade against a bright blue sky"></div>
  <div class="card-icon"><svg width="44" height="44" viewBox="0 0 44 44"><rect x="4" y="4" width="36" height="36" fill="none" stroke="#fff" stroke-width="3"/><path d="M4 4l12 6v30M40 4l-12 6v30" fill="none" stroke="#fff" stroke-width="3"/></svg></div>
  <h3 class="card-title">Commercial &amp; Residential</h3>
  <p class="card-sub">Your Valley Commercial Film Experts!</p>
  <div class="card-body">
    <p>Window film is a sheet of coating that, with proper installation by Saguaro Tint, can deliver energy savings similar to that offered by premium replacement windows — but without the expense of replacement. On existing home windows, including dual pane and low e, the process is usually complete in no more than two days, with immediate improvements in comfort, efficiency and glare reduction.</p>
    <p>A wide range of protective film is available. These include anti-graffiti, nonreflective, decorative, dual-reflective and ceramic. Choose, too, from many shades, almost clear to dark. And, because window film is considered carbon-negative, some products qualify for sustainable home credits and energy rebates.</p>
  </div>
</article>

<!-- Vehicle wraps -->
<article class="card abs" style="left:100px;top:1369px">
  <div class="card-photo photo-wraps" role="img" aria-label="Side mirror of a car driving on a blurred road"></div>
  <div class="card-icon"><svg width="48" height="40" viewBox="0 0 48 40"><path d="M4 8q20-8 40 0l-5 26H9z" fill="none" stroke="#fff" stroke-width="3" stroke-linejoin="round"/><path d="M14 24l8-8M22 28l10-10M28 22l6-6" stroke="#fff" stroke-width="2.5"/></svg></div>
  <h3 class="card-title">Vehicle Wraps</h3>
  <p class="card-sub">An easy solution to a boring car</p>
  <div class="card-body">
    <p>Want to change the look of your car or truck without harming the factory finish? Saguaro Tint's professional team can install premium Norvane 1080 film to change the look of your vehicle while maintaining its original color for resale or to return to when your requirements or mood change.</p>
    <p>Individuals and fleet owners enjoy the process because most vehicles can be wrapped within two to three days, and our professional installers can also remove it without damaging the original paint.</p>
    <p>Matte Metallic is popular now, and you can choose from Carbon Fiber, Matte and Brushed Metallic Colors, including 15 new shades.</p>
  </div>
</article>

<!-- Clear bra -->
<article class="card abs" style="left:644px;top:1369px">
  <div class="card-photo photo-bra" role="img" aria-label="Hands smoothing protective film onto a dark car surface"></div>
  <div class="card-icon"><svg width="46" height="40" viewBox="0 0 46 40"><path d="M4 4h26l10 12v20H4z" fill="none" stroke="#fff" stroke-width="3" stroke-linejoin="round"/><circle cx="16" cy="18" r="5" fill="#fff"/><path d="M8 32q8-10 16 0" fill="#fff"/></svg></div>
  <h3 class="card-title">Clear Bra</h3>
  <p class="card-sub">Your Valley Commercial Film Experts!</p>
  <div class="card-body">
    <p>Clear bra, or Paint Protection Film (PPF), is a clear urethane that certified Saguaro Tint installers attach to the finish of those areas of your vehicle prone to minor impacts, such as your hood and bumper. Practically invisible, this durable film protects any vehicle from nicks, chips, abrasions and scuffs, and PPF can also protect your head-lights from yellowing and hazing.</p>
    <p>Race tested to 160-plus mph, clear bra requires minor maintenance, can be waxed, is car wash friendly, easily removable, and Saguaro Tint uses Clearguard software to eliminate hand-cutting or bulking. This "cosmetic protection for your car" can improve the resale value of your car, truck, boat or other vehicle. And, we stand by our experi-enced professionals with a five-year paint-protection warranty.</p>
  </div>
</article>

<div class="map abs" role="img" aria-label="Street map of the shop's neighbourhood with a location pin"></div>
<svg class="abs" style="left:588px;top:2300px" width="24" height="34" viewBox="0 0 24 34"><path d="M12 0a12 12 0 00-12 12c0 9 12 22 12 22s12-13 12-22A12 12 0 0012 0z" fill="#e0342b"/><circle cx="12" cy="12" r="4" fill="#9b1a14"/></svg>

<footer>
  <svg class="footer-edge abs" viewBox="0 0 1200 40" preserveAspectRatio="none"><path d="M0 40 L0 10 Q600 -10 1200 10 L1200 40 Z" fill="#1f1f1f"/></svg>
  <div class="footer abs"></div>

  <h4 class="foot-head abs" style="left:100px;top:2578px">QUICK LINK</h4>
  <ul class="foot-links abs" style="left:100px;top:2622px">
    <li>Home</li><li>Window Film Services</li><li>Film</li><li>About</li><li>Gallery</li><li>Contact</li>
  </ul>

  <h4 class="foot-head abs" style="left:314px;top:2578px">CONTACT US</h4>
  <div class="contact-line abs" style="left:314px;top:2628px">
    <svg width="12" height="16" viewBox="0 0 12 16"><path d="M6 0a6 6 0 00-6 6c0 4.5 6 10 6 10s6-5.5 6-10A6 6 0 006 0z" fill="#fff"/><circle cx="6" cy="6" r="2" fill="#1a1a1a"/></svg>
    <span>Saguaro Window Tinting,<br>418 Palo Verde Rd, Mesa AZ</span>
  </div>
  <div class="contact-line abs" style="left:314px;top:2684px">
    <svg width="12" height="14" viewBox="0 0 24 24"><path d="M6.6 10.8a15 15 0 006.6 6.6l2.2-2.2c.3-.3.7-.4 1-.2 1.1.4 2.3.6 3.6.6.6 0 1 .4 1 1V20c0 .6-.4 1-1 1C10.6 21 3 13.4 3 4c0-.6.4-1 1-1h3.5c.6 0 1 .4 1 1 0 1.3.2 2.5.6 3.6.1.3 0 .7-.2 1z" fill="#fff"/></svg>
    <span>Phone : 480.555.0147</span>
  </div>
  <div class="contact-line abs" style="left:314px;top:2714px">
    <svg width="13" height="14" viewBox="0 0 14 11"><rect x=".75" y=".75" width="12.5" height="9.5" fill="none" stroke="#fff" stroke-width="1.5"/><path d="M1 1l6 5 6-5" fill="none" stroke="#fff" stroke-width="1.5"/></svg>
    <span>Email : info@saguarotint.example</span>
  </div>

  <h4 class="foot-head abs" style="left:633px;top:2578px">GET A QUOTE</h4>
  <p class="quote-text abs" style="left:633px;top:2616px;width:470px">Lorem ipsum dolor sit amet, consectetur adipiscing elit, sed do eiusmod tempor incidi-dunt ut labore et dolore magna aliqua. Ut enim ad minim veniam.</p>
  <div class="field abs" style="left:633px;top:2674px;width:226px">Name</div>
  <div class="field abs" style="left:876px;top:2674px;width:226px">E - Mail</div>
  <div class="field abs" style="left:633px;top:2724px;width:226px">Phone No</div>
  <div class="signup abs" style="left:876px;top:2724px;width:226px">SIGNUP NOW</div>

  <div class="bottom-bar abs"></div>
  <p class="copyright abs">© 2017 Saguaro Window Tinting. All Rights Reserved.</p>
  <div class="foot-brand abs"><span class="brand-dot"></span><span class="brand-name">Saguaro Window Tint</span></div>
  <div class="foot-social abs"><i></i><i></i><i></i><i></i></div>
</footer>

</body>
</html>
```